Letter head / email signature/ contract document templates

We need a professional email signature and letterhead designed for our established carpentry and maintenance company. Our Logo (attached) was originally designed 6 years ago by design guru and we love it, looking for something to compliment it ( not a home job)

```html
<!DOCTYPE html>
<html lang="en">
<head>
<meta charset="utf-8">
<title>Corbett Build &amp; Repair – Stationery</title>
<link href="https://fonts.googleapis.com/css2?family=Open+Sans:wght@400;600;700&display=swap" rel="stylesheet">
<style>
  :root {
    --backdrop: #d6d6d6;
    --paper: #f4f4f4;
    --ink: #4a4a4a;
    --ink-soft: #6b6b6b;
    --charcoal: #3d3d3d;
    --brand-red: #e0323a;
    --brand-red-deep: #c8262e;
  }
  * { box-sizing: border-box; margin: 0; padding: 0; }
  html, body { width: 1200px; height: 800px; overflow: hidden; }
  body {
    background: var(--backdrop);
    font-family: "Open Sans", Arial, sans-serif;
    color: var(--ink);
    position: relative;
  }

  /* Letterhead */
  .letterhead {
    position: absolute; left: 90px; top: 30px;
    width: 520px; height: 740px;
    background: var(--paper);
    padding: 50px 46px 0;
  }
  .letterhead__top { display: flex; justify-content: space-between; align-items: flex-start; }
  .brand-name {
    display: flex; align-items: center; gap: 8px;
    font-weight: 700; color: var(--charcoal); line-height: 1.1;
  }
  .brand-name__dot { width: 12px; height: 12px; background: var(--brand-red); flex: none; }
  .letterhead .brand-name { font-size: 24px; margin-top: 6px; }
  .letterhead .brand-name__dot { width: 16px; height: 16px; }
  .contact-list { list-style: none; font-size: 8.5px; line-height: 1.45; color: var(--ink-soft); }
  .contact-list li { display: flex; align-items: center; gap: 4px; }
  .contact-list svg { width: 7px; height: 7px; fill: var(--brand-red); flex: none; }

  .letter { margin-top: 66px; font-size: 9.6px; line-height: 1.55; color: var(--ink-soft); }
  .letter p { margin-bottom: 13px; text-align: justify; }
  .signature {
    width: 70px; height: 56px; margin-top: 8px;
    background: linear-gradient(135deg, #e6e6e6, #d9d9d9);
  }

  .stripe {
    position: absolute; left: 0; right: 0; bottom: 0; height: 11px;
    display: flex; gap: 4px;
  }
  .stripe__dark { width: 8%; background: var(--charcoal); }
  .stripe__red { flex: 1; background: var(--brand-red); margin-right: 34px; }

  /* Business cards */
  .card {
    position: absolute; width: 480px; height: 270px;
  }
  .card--front { left: 660px; top: 120px; background: var(--paper); padding: 34px 34px 0; }
  .card--back {
    left: 660px; top: 420px;
    background: linear-gradient(135deg, var(--brand-red-deep), var(--brand-red));
    display: flex; flex-direction: column; align-items: center; justify-content: center;
  }
  .card__row { display: flex; justify-content: space-between; }
  .card__name { font-size: 20px; font-weight: 600; color: var(--charcoal); }
  .card__role { font-size: 14px; color: var(--brand-red); margin-bottom: 18px; }
  .card .contact-list { font-size: 11px; line-height: 1.55; }
  .card .contact-list svg { width: 9px; height: 9px; }
  .card--front .brand-name { font-size: 20px; margin-top: 4px; }
  .card__social {
    position: absolute; right: 34px; bottom: 44px;
    display: flex; align-items: center; gap: 4px; font-size: 11px; color: var(--ink-soft);
  }
  .card__social span.dot { width: 10px; height: 10px; border-radius: 50%; background: var(--brand-red); }
  .card--back .brand-name { color: #fff; font-size: 30px; }
  .card--back .brand-name__dot { background: #fff; width: 18px; height: 18px; }
  .card__web { color: #fff; font-size: 11px; margin-top: 44px; opacity: .9; }
</style>
</head>
<body>

<article class="letterhead">
  <header class="letterhead__top">
    <div class="brand-name"><span class="brand-name__dot"></span>Corbett Build &amp; Repair</div>
    <ul class="contact-list">
      <li>14 Linden Row,</li>
      <li>Eastbrook, ON K2P 4R7</li>
      <li><svg viewBox="0 0 10 10"><path d="M2 0h2l1 3-1.5 1a6 6 0 0 0 2.5 2.5L7 5l3 1v2l-1 2C4 10 0 6 0 1z"/></svg>555.204.1180</li>
      <li><svg viewBox="0 0 10 10"><rect y="2" width="10" height="6"/></svg>hello@corbettrepair.com</li>
      <li><svg viewBox="0 0 10 10"><circle cx="5" cy="5" r="5"/></svg>www.corbettrepair.com</li>
    </ul>
  </header>

  <section class="letter">
    <p>Dear customer,</p>
    <p>Lorem ipsum dolor sit amet, consectetur adipisicing elit, sed do eiusmod tempor incididunt ut labore et dolore magna aliqua. Ut enim ad minim veniam, quis nostrud exercitation ullamco laboris nisi ut aliquip ex ea commodo consequat. Duis aute irure dolor in reprehenderit in voluptate velit esse cillum dolore eu fugiat nulla pariatur. Excepteur sint occaecat cupidatat non proident, sunt in culpa qui officia deserunt mollit anim id est laborum.</p>
    <p>Lorem ipsum dolor sit amet, consectetur adipisicing elit, sed do eiusmod tempor incididunt ut labore et dolore magna aliqua. Ut enim ad minim veniam, quis nostrud exercitation ullamco laboris nisi ut aliquip ex ea commodo consequat. Duis aute irure dolor in reprehenderit in voluptate velit esse cillum dolore eu fugiat nulla pariatur. Excepteur sint occaecat cupidatat non proident, sunt in culpa qui officia deserunt mollit anim id est laborum.</p>
    <p>Lorem ipsum dolor sit amet, consectetur adipisicing elit, sed do eiusmod tempor incididunt ut labore et dolore magna aliqua. Ut enim ad minim veniam, quis nostrud exercitation ullamco laboris nisi ut aliquip ex ea commodo consequat. Duis aute irure dolor in reprehenderit in voluptate velit esse cillum dolore eu fugiat nulla pariatur. Excepteur sint occaecat cupidatat non proident, sunt in culpa qui officia deserunt mollit anim id est laborum.</p>
    <p>Lorem ipsum dolor sit amet, consectetur adipisicing elit, sed do eiusmod tempor incididunt ut labore et dolore magna aliqua. Ut enim ad minim veniam, quis nostrud exercitation ullamco laboris nisi ut aliquip ex ea commodo consequat. Duis aute irure dolor in reprehenderit.</p>
    <p>Yours Sincerely,</p>
    <div class="signature" role="img" aria-label="Handwritten signature"></div>
  </section>

  <div class="stripe"><span class="stripe__dark"></span><span class="stripe__red"></span></div>
</article>

<article class="card card--front">
  <div class="card__row">
    <div>
      <h2 class="card__name">TOM REYES</h2>
      <p class="card__role">Director</p>
      <ul class="contact-list">
        <li>14 Linden Row,</li>
        <li>Eastbrook, ON K2P 4R7</li>
        <li><svg viewBox="0 0 10 10"><path d="M2 0h2l1 3-1.5 1a6 6 0 0 0 2.5 2.5L7 5l3 1v2l-1 2C4 10 0 6 0 1z"/></svg>555.204.1180</li>
        <li><svg viewBox="0 0 10 10"><rect y="2" width="10" height="6"/></svg>hello@corbettrepair.com</li>
        <li><svg viewBox="0 0 10 10"><circle cx="5" cy="5" r="5"/></svg>www.corbettrepair.com</li>
      </ul>
    </div>
    <div class="brand-name"><span class="brand-name__dot"></span>Corbett Build &amp; Repair</div>
  </div>
  <div class="card__social"><span class="dot"></span><span class="dot"></span><span class="dot"></span>@corbettrepair</div>
  <div class="stripe"><span class="stripe__dark"></span><span class="stripe__red"></span></div>
</article>

<article class="card card--back">
  <div class="brand-name"><span class="brand-name__dot"></span>Corbett Build &amp; Repair</div>
  <p class="card__web">www.corbettrepair.com</p>
</article>

</body>
</html>
```